3rd Annual Suds & Wags Fundraiser

This is our 3rd Annual Suds & Wags Dog Wash Extravagana to support Helpers of Tamsin Valley Pet Center. Please see the attached flyer for the 2nd Annual. We loved this flyer! Please revamp with our logo attached and the new content provided. Let's keep to the same colors as the 2nd Annual flyer-no change. Date: Saturday April 25th 2020 10A-1PM. Rain Date: May 2nd. Same address as 2nd Annual.

Other font styles liked:
• See 2nd Annual Flyer

Colors
add136
e34297
6b449b

Requirements
Must have
• See attached 2nd annual flyer including colors
Nice to have

```html
<!DOCTYPE html>
<html lang="en">
<head>
<meta charset="utf-8">
<title>3rd Annual Suds &amp; Wags</title>
<link rel="stylesheet" href="https://fonts.googleapis.com/css2?family=Fredoka:wght@500;600;700&family=Archivo:wght@500;600;700&display=swap">
<style>
  :root {
    --green: #add136;
    --pink: #e34297;
    --purple: #6b449b;
    --purple-soft: #8a6ab5;
    --mat: #6d6e71;
    --ink: #1a1a1a;
    --white: #ffffff;
  }
  html, body { margin: 0; padding: 0; width: 960px; height: 1200px; overflow: hidden; background: var(--mat); }
  p, ul { margin: 0; }
  .stage { position: relative; width: 1200px; height: 1500px; transform: scale(0.8); transform-origin: 0 0; }
  .flyer { position: absolute; left: 93px; top: 33px; width: 1014px; height: 1434px; background: var(--white); overflow: hidden; }
  .art { position: absolute; left: 0; top: 0; width: 1014px; height: 1434px; }
  .photo-corner { position: absolute; left: 0; top: 0; width: 1014px; height: 1434px; z-index: 2; pointer-events: none; }
  .abs { position: absolute; margin: 0; }

  .edition { left: 60px; top: 548px; font: 700 64px/1 "Fredoka", sans-serif; color: var(--pink); }
  .annual { left: 54px; top: 604px; font: 700 68px/1 "Fredoka", sans-serif; color: var(--purple-soft); }
  .event-name { left: 52px; top: 690px; font: 700 60px/1 "Fredoka", sans-serif; color: var(--purple-soft); }
  .slogan { left: 54px; top: 758px; font: 600 17px/1 "Archivo", sans-serif; letter-spacing: 7px; color: var(--pink); }

  .support-label { left: 736px; top: 530px; font: 700 31px/1 "Archivo", sans-serif; color: var(--purple); letter-spacing: 0.5px; }
  .partner { left: 745px; top: 600px; width: 230px; display: flex; align-items: center; gap: 12px; }
  .partner-dot { flex: none; width: 34px; height: 34px; border-radius: 50%; background: var(--ink); }
  .partner-name { font: 700 26px/1.15 "Archivo", sans-serif; color: var(--ink); }
  .partner-note { left: 745px; top: 730px; width: 230px; text-align: center; font: 500 15px/1.35 "Archivo", sans-serif; color: var(--ink); }

  .headline { left: 80px; top: 795px; width: 854px; height: 64px; border-radius: 32px; background: var(--pink);
    color: var(--white); font: 600 42px/64px "Fredoka", sans-serif; text-align: center; }

  .when { left: 36px; top: 869px; width: 523px; height: 148px; border-radius: 10px; background: var(--purple-soft); color: var(--white); }
  .when-row { position: absolute; left: 14px; font: 500 30px/1 "Archivo", sans-serif; }
  .when-row b { font: 600 36px/1 "Fredoka", sans-serif; margin-right: 10px; }
  .where { left: 597px; top: 869px; width: 376px; height: 148px; border-radius: 10px; background: var(--purple-soft); color: var(--white); }
  .where-title { position: absolute; left: 20px; top: 12px; font: 600 36px/1 "Fredoka", sans-serif; }
  .where-address { position: absolute; left: 20px; top: 58px; font: 600 20px/1.35 "Archivo", sans-serif; white-space: nowrap; }

  .perks { left: 36px; top: 1034px; width: 906px; height: 200px; border-radius: 12px; background: var(--green); color: var(--ink); z-index: 1; }
  .perk-list { position: absolute; top: 14px; list-style: none; padding: 0; font: 600 19px/26px "Archivo", sans-serif; }
  .perk-list li { display: flex; align-items: flex-start; gap: 10px; }
  .tick { flex: none; width: 15px; height: 15px; margin-top: 5px; }
  .donate-line { position: absolute; left: 22px; top: 106px; font: 600 17px/1 "Archivo", sans-serif; display: flex; align-items: center; gap: 8px; }
  .donate-link { color: var(--white); }
  .donate-button { background: var(--purple-soft); color: var(--white); border-radius: 14px; padding: 6px 12px; margin-left: 6px; }
  .perk-note { position: absolute; left: 22px; top: 144px; width: 640px; font: 600 17px/1.25 "Archivo", sans-serif; }

  .contact { top: 1262px; font: 600 18px/1.3 "Archivo", sans-serif; color: var(--ink); z-index: 3; }
  .contact-name { display: block; font: 600 28px/1.2 "Fredoka", sans-serif; color: var(--pink); margin-bottom: 4px; }
</style>
</head>
<body>
<div class="stage">
  <div class="flyer">
    <svg class="art" viewBox="0 0 1014 1434" xmlns="http://www.w3.org/2000/svg">
      <defs>
        <linearGradient id="crowdTone" x1="0" y1="0" x2="1" y2="1">
          <stop offset="0" stop-color="#9fb7c9"/>
          <stop offset="0.45" stop-color="#7e9a66"/>
          <stop offset="0.8" stop-color="#b89a7c"/>
          <stop offset="1" stop-color="#d9d2c4"/>
        </linearGradient>
        <linearGradient id="spotTone" x1="0" y1="0" x2="1" y2="1">
          <stop offset="0" stop-color="#c9d3dc"/>
          <stop offset="0.6" stop-color="#8f8a80"/>
          <stop offset="1" stop-color="#3b3b40"/>
        </linearGradient>
      </defs>

      <path d="M0 0 H1014 V150 C820 230 560 370 0 430 Z" fill="url(#crowdTone)" role="img" aria-label="Photo of teen volunteers and a dog mascot costume posing outdoors"/>
      <path d="M0 430 C380 400 640 300 1014 150 V175 C720 330 420 470 0 560 Z" fill="var(--green)"/>
      <path d="M0 560 C300 490 520 450 700 400 C520 470 300 530 0 590 Z" fill="var(--purple-soft)"/>
      <path d="M880 190 C930 170 980 160 1014 150 V172 C970 178 925 190 880 205 Z" fill="var(--purple-soft)"/>
      <path d="M900 178 C940 164 985 154 1014 140 V150 C975 162 935 172 900 186 Z" fill="var(--green)"/>

      <circle cx="337" cy="502" r="100" fill="var(--purple-soft)"/>
      <circle cx="337" cy="502" r="90" fill="url(#spotTone)" role="img" aria-label="Photo of a volunteer with a dog in an orange bandana"/>
      <circle cx="587" cy="500" r="130" fill="var(--green)"/>
      <circle cx="587" cy="500" r="118" fill="url(#spotTone)" role="img" aria-label="Photo of a welcome banner at the dog wash station"/>
      <circle cx="840" cy="335" r="160" fill="var(--pink)"/>
      <circle cx="840" cy="335" r="148" fill="var(--white)"/>
      <circle cx="840" cy="335" r="136" fill="url(#crowdTone)" role="img" aria-label="Photo of children and a man with a dog at the event tents"/>

      <path d="M0 1407 H740 V1434 H0 Z" fill="var(--purple-soft)"/>
    </svg>

    <svg class="photo-corner" viewBox="0 0 1014 1434" xmlns="http://www.w3.org/2000/svg">
      <defs>
        <linearGradient id="washTone" x1="0" y1="0" x2="0" y2="1">
          <stop offset="0" stop-color="#e7e2dc"/>
          <stop offset="0.5" stop-color="#b98a64"/>
          <stop offset="1" stop-color="#8f97a3"/>
        </linearGradient>
      </defs>
      <path d="M750 1434 C720 1290 740 1110 840 1020 C920 1000 990 1002 1014 1010 V1434 Z" fill="var(--purple-soft)"/>
      <path d="M772 1434 C744 1296 764 1124 856 1036 C928 1018 990 1020 1014 1026 V1434 Z" fill="url(#washTone)" role="img" aria-label="Photo of a girl hugging a wet spaniel during its bath"/>
    </svg>

    <p class="abs edition">3rd</p>
    <p class="abs annual">Annual</p>
    <p class="abs event-name">Suds &amp; Wags</p>
    <p class="abs slogan">DO A LITTLE. CHANGE A LOT.</p>

    <p class="abs support-label">INSUPPORT OF</p>
    <div class="abs partner">
      <span class="partner-dot"></span>
      <span class="partner-name">Helpers of Tamsin Valley Pet Center</span>
    </div>
    <p class="abs partner-note">Adopt a forever friend …<br>You will be their hero</p>

    <p class="abs headline">A FAMILY FUN EVENT FOR ALL AGES</p>

    <div class="abs when">
      <p class="when-row" style="top:22px"><b>DATE:</b>Saturday April 25th 2020</p>
      <p class="when-row" style="top:62px"><b>TIME:</b> 10A-1PM.</p>
      <p class="when-row" style="top:108px">Rain Date: May 2nd</p>
    </div>

    <div class="abs where">
      <p class="where-title">Location:</p>
      <p class="where-address">Harborline Realty, 418 Meadowgate<br>Ave. Coral Bend FL 32999<br>Larkwood Town Center</p>
    </div>

    <div class="abs perks">
      <ul class="perk-list" style="left:22px">
        <li><svg class="tick" viewBox="0 0 15 15"><rect x="1" y="1" width="13" height="13" fill="none" stroke="currentColor" stroke-width="1.6"/><path d="M3.5 7.5 L6.5 10.5 L12 3.5" fill="none" stroke="currentColor" stroke-width="2"/></svg>Free Doggie Wash</li>
        <li><svg class="tick" viewBox="0 0 15 15"><rect x="1" y="1" width="13" height="13" fill="none" stroke="currentColor" stroke-width="1.6"/><path d="M3.5 7.5 L6.5 10.5 L12 3.5" fill="none" stroke="currentColor" stroke-width="2"/></svg>Food &amp; Beverages</li>
        <li><svg class="tick" viewBox="0 0 15 15"><rect x="1" y="1" width="13" height="13" fill="none" stroke="currentColor" stroke-width="1.6"/><path d="M3.5 7.5 L6.5 10.5 L12 3.5" fill="none" stroke="currentColor" stroke-width="2"/></svg>Vendors (FREE give-a-ways)</li>
      </ul>
      <ul class="perk-list" style="left:338px">
        <li><svg class="tick" viewBox="0 0 15 15"><rect x="1" y="1" width="13" height="13" fill="none" stroke="currentColor" stroke-width="1.6"/><path d="M3.5 7.5 L6.5 10.5 L12 3.5" fill="none" stroke="currentColor" stroke-width="2"/></svg>Raffle Drawings</li>
        <li><svg class="tick" viewBox="0 0 15 15"><rect x="1" y="1" width="13" height="13" fill="none" stroke="currentColor" stroke-width="1.6"/><path d="M3.5 7.5 L6.5 10.5 L12 3.5" fill="none" stroke="currentColor" stroke-width="2"/></svg>Grand Prize</li>
        <li><svg class="tick" viewBox="0 0 15 15"><rect x="1" y="1" width="13" height="13" fill="none" stroke="currentColor" stroke-width="1.6"/><path d="M3.5 7.5 L6.5 10.5 L12 3.5" fill="none" stroke="currentColor" stroke-width="2"/></svg>Donations Welcome</li>
      </ul>
      <ul class="perk-list" style="left:564px">
        <li><svg class="tick" viewBox="0 0 15 15"><rect x="1" y="1" width="13" height="13" fill="none" stroke="currentColor" stroke-width="1.6"/><path d="M3.5 7.5 L6.5 10.5 L12 3.5" fill="none" stroke="currentColor" stroke-width="2"/></svg>Adoptions by<br>HOTVPC</li>
      </ul>
      <p class="donate-line">To Make a Donation: <span class="donate-link">https://www.hotvpc.org/give/</span><span class="donate-button">CLICK: DONATE</span></p>
      <p class="perk-note">All domestic breeds from puppies to seniors invited. Please be sure furry Fido is tolerant of other dogs, crowds and bathing.</p>
    </div>

    <p class="abs contact" style="left:36px"><span class="contact-name">MARISSA DELANE</span>Harborline Realty Corp.<br>555.210.4418<br>marissadelane@harborlinerealty.com</p>
    <p class="abs contact" style="left:429px"><span class="contact-name">JOANNA WHITFIELD</span>HOTVPC<br>555.384.9021<br>joanna-whitfield@mailbox.net</p>
  </div>
</div>
</body>
</html>
```